Business card design for Automotive workshop

We need a business card for a new automotive repair and tyre shop called Keelstone Prime Automotive located in New Zealand. We are a clean, modern and fresh workshop and company.

Front needs to feature logo,
my name:
Marlo Fenwicke (director)

Address:
48 Tarn Lane
Harrowby 3592

Phone: 07 594 2713
Mobile: 027 451 9362
Email: office@keelstoneautomotive.example.nz
Website: keelstoneautomotive.example.nz

Back needs to feature an area to write down appointment details, date and time.

Also feature a list of jobs and work we do such as,
Vehicle Servicing
All Mechanical Repairs
Warrant of Fitness
Tyres & Wheel Alignments
Automotive Diagnostics
Automotive Parts & Supplies

```html
<!DOCTYPE html>
<html lang="en">
<head>
<meta charset="utf-8">
<title>Keelstone Prime Automotive – Business Card</title>
<link href="https://fonts.googleapis.com/css2?family=Roboto:wght@400;500;700&display=swap" rel="stylesheet">
<style>
  :root {
    --page: #d9d6d2;
    --card: #2a2a2c;
    --red: #e3252b;
    --white: #f2f2f2;
    --mark-dark: #4b4b4e;
    --rule: #8a8a8c;
  }
  * { box-sizing: border-box; margin: 0; padding: 0; }
  html, body {
    width: 1200px; height: 900px; overflow: hidden;
    background: var(--page);
    font-family: "Roboto", Arial, sans-serif;
  }
  .card {
    position: absolute; left: 250px; width: 700px; height: 400px;
    background: var(--card);
    box-shadow: 0 6px 18px rgba(0,0,0,.25);
  }
  .card--back { top: 40px; }
  .card--front { top: 460px; }

  .brand {
    position: absolute; display: flex; align-items: center; gap: 12px;
    font-weight: 700; text-transform: uppercase; letter-spacing: 1px; line-height: 1.1;
  }
  .brand__square { width: 14px; height: 14px; flex: none; }
  .card--back .brand { left: 190px; top: 50px; width: 360px; font-size: 30px; color: var(--mark-dark); }
  .card--back .brand__square { background: var(--mark-dark); }
  .card--front .brand { left: 40px; top: 130px; width: 320px; font-size: 28px; color: var(--red); }
  .card--front .brand__square { background: var(--red); }

  .appointment__title {
    position: absolute; top: 150px; left: 0; right: 0; text-align: center;
    color: var(--red); font-size: 22px; font-weight: 500; letter-spacing: .5px;
  }
  .appointment__fields {
    position: absolute; top: 215px; left: 40px; right: 40px;
    display: flex; gap: 16px; color: var(--white); font-size: 17px;
  }
  .field { flex: 1; display: flex; align-items: flex-end; gap: 6px; }
  .field__line { flex: 1; border-bottom: 1px solid var(--rule); height: 14px; }
  .appointment__days {
    position: absolute; top: 290px; left: 100px; right: 60px;
    display: flex; justify-content: space-between; color: var(--white); font-size: 17px;
  }
  .day { display: flex; align-items: center; gap: 8px; }
  .day__circle { width: 16px; height: 16px; border: 1.5px solid var(--red); border-radius: 50%; }

  .contact__divider {
    position: absolute; left: 375px; top: 70px; width: 1.5px; height: 180px; background: var(--red);
  }
  .contact { position: absolute; left: 392px; top: 62px; right: 20px; color: var(--white); }
  .contact__name { color: var(--red); font-size: 28px; font-weight: 700; }
  .contact__role { font-size: 18px; margin-bottom: 10px; }
  .contact__list { list-style: none; font-size: 15px; }
  .contact__list li { display: flex; align-items: center; gap: 7px; height: 22px; white-space: nowrap; }
  .contact__list svg { width: 13px; height: 13px; flex: none; fill: var(--red); }

  .services {
    position: absolute; left: 0; right: 0; bottom: 40px; text-align: center;
    color: var(--white); font-size: 16px; line-height: 1.5;
  }
  .services__dot { color: var(--red); margin: 0 5px; }
</style>
</head>
<body>

<section class="card card--back">
  <div class="brand"><span class="brand__square"></span><span>Keelstone Prime Automotive</span></div>
  <h2 class="appointment__title">APPOINTMENT</h2>
  <div class="appointment__fields">
    <div class="field"><span>Date:</span><span class="field__line"></span></div>
    <div class="field"><span>Time:</span><span class="field__line"></span></div>
  </div>
  <div class="appointment__days">
    <span class="day"><span class="day__circle"></span>Mon</span>
    <span class="day"><span class="day__circle"></span>Tue</span>
    <span class="day"><span class="day__circle"></span>Wed</span>
    <span class="day"><span class="day__circle"></span>Thu</span>
    <span class="day"><span class="day__circle"></span>Fri</span>
  </div>
</section>

<section class="card card--front">
  <div class="brand"><span class="brand__square"></span><span>Keelstone Prime Automotive</span></div>
  <div class="contact__divider"></div>
  <div class="contact">
    <p class="contact__name">Marlo Fenwicke</p>
    <p class="contact__role">director</p>
    <ul class="contact__list">
      <li><svg viewBox="0 0 16 16"><path d="M3 1l3 3-1.5 2a9 9 0 005.5 5.5L12 10l3 3-2 2C7 15 1 9 1 3z"/></svg>07 594 2713</li>
      <li><svg viewBox="0 0 16 16"><path d="M4 0h8v16H4zM5.5 2v10h5V2z"/></svg>027 451 9362</li>
      <li><svg viewBox="0 0 16 16"><path d="M0 3h16v10H0zM1.5 4.5L8 9l6.5-4.5V4h-13z"/></svg>office@keelstoneautomotive.example.nz</li>
      <li><svg viewBox="0 0 16 16"><path d="M8 0a8 8 0 100 16A8 8 0 008 0zm0 2a6 6 0 013 .8L9 5 6 4 3 6a6 6 0 015-4zm-6 7l3 1 1 3 2 1a6 6 0 01-6-5zm8 4.7l1-2.7 3-2a6 6 0 01-4 4.7z"/></svg>keelstoneautomotive.example.nz</li>
      <li><svg viewBox="0 0 16 16"><path d="M8 0a5.5 5.5 0 015.5 5.5C13.5 10 8 16 8 16S2.5 10 2.5 5.5A5.5 5.5 0 018 0zm0 3.5a2 2 0 100 4 2 2 0 000-4z"/></svg>48 Tarn Lane, Harrowby 3592</li>
    </ul>
  </div>
  <div class="services">
    <p>Vehicle Servicing<span class="services__dot">•</span>All Mechanical Repairs<span class="services__dot">•</span>Warrant of Fitness</p>
    <p>Tyres &amp; Wheel Alignments<span class="services__dot">•</span>Automotive Diagnostics<span class="services__dot">•</span>Automotive Parts &amp; Supplies</p>
  </div>
</section>

</body>
</html>
```